Website Redesign for a faith-based, not-for-profit health and human services organization

New website design for the Harvest Hope Outreach House.
- Current site: www.hhohbriel.org -
We are looking for a nice clean, simple, friendly-yet-elegant website layout.
Colors are #f5eed5 (cream), #FFFFFF (white), and all logo colors.
Design a layout for home page
Design a layout for general layouts
-layout only no html needed (preferably a high res PSD file format) -
Main menu should be along top with side navigation for submenu, no side menu on home page.
Also would be open to seeing some updated colors on the logo design, currently the colors are slightly outdated. The Vine of Plenty quilt design fits the organization’s mission and the rural farming / Amish-Mennonite-Brethren community around us.

ADDITIONAL PAGES AND MENU STRUCTURE ON NEW SITE

- How to Help
... Volunteer
... Donate Time
... Donate Money
... Donate Supplies
... Current Needs

- Programs

- News & Events
... Upcoming Events
... Upcoming Fundraisers
... Newsletter

- Our Partners

- About Us
... Overview
... Mission
... Staff Directory
... Board of Directors
... Annual Reports

- Contact

Our annual special event is Gather at the Hearth and should be integrated into the home page - see attached logos and banner

Websites with elements we like (from organizations doing similar work), each for a different reason....

1. http://www.kinbridgeroutes.org
Good design, color, clarity on this site. Multi-dimensional, photos...easy interaction, etc.

2. http://endemptyplates.org
Quite simple, nothing fancy, but some good basic stuff here, and pretty easy to navigate...

3. http://www.townfolkhub.org
Intrigued by the bulletin board design and the way they have their programs broken down to show impact, needs, etc. It has a lot of good information, but is really too verbose, some of the print is too small, etc. Not perfect, but some interesting design elements.

4. http://sharedlarder.org
Site is boring and not very well designed, but it has some of the features that we would like to see at the top, donations, partners, etc.

5. http://www.bellmerefoodshelf.org
Too many listings on the sidebar - needs to be cleaner & simpler, but a lot of good information and we like the way they show volunteer photos on the Thanks to Our Helpers page...

About
Harvest Hope Outreach House ("HHOH" or “the Center”) is a faith-based non-for-profit health and human services organization that exists as an outreach of and for the Ordell-Bray Area School District.
Tagline: Mercy at Work (we work to serve the needs of the ‘least of these’ with compassion).

Mission
Our mission is to see lives transformed and the community enhanced by encouraging the oppressed, defending the cause of the weak and maintaining the rights of the poor - bringing together the resources of a caring community as a demonstration of the good news of Christ.

Company Overview
Harvest Hope Outreach House works closely with the community in which it serves. A tremendous value is placed upon the partnerships that have formed with caring people within the community and with organizations that share the goal of bringing together resources to help those who need it most. Individuals, volunteers, churches, corporations, foundations, and government sources all pull together to help make our mission possible.

Since 1996 the Harvest Hope Outreach House has collaboratively worked to see our community enhanced, adapting programs and services to meet the changing needs of the community.

Target Market(s)

people needing assistance in local community

Industry/Entity Type

Government

Requirements
Must have
• Good social button integration
Should not have
• No Find Us page like old website it is not needed

```html
<!DOCTYPE html>
<html lang="en">
<head>
<meta charset="utf-8">
<title>Harvest Hope Outreach House</title>
<link rel="stylesheet" href="https://fonts.googleapis.com/css2?family=Yanone+Kaffeesatz:wght@400;500&family=Ubuntu:ital,wght@0,400;0,500;1,400;1,500&family=Libre+Baskerville&family=Arimo:wght@400&display=swap">
<style>
:root{
  --maroon:#7b1729;
  --maroon-dark:#5e0f1e;
  --cream:#f7f2e2;
  --white:#ffffff;
  --green:#13472a;
  --green-dark:#0c3520;
  --green-soft:#6f9a80;
  --gold:#c9a553;
  --tan-text:#dcbd8c;
  --tan:#b7a47c;
  --ink:#6b6b6b;
  --heading:#1d4a2a;
  --red-text:#b3113c;
  --badge:#8f8f8f;
}
*{box-sizing:border-box;margin:0;padding:0}
html,body{width:929px;height:1200px;overflow:hidden}
body{position:relative;background:var(--cream);font-family:"Arimo",Arial,sans-serif}
.abs{position:absolute}
.top-band{left:0;top:0;width:929px;height:352px;background:var(--maroon)}
.footer-band{left:0;top:1089px;width:929px;height:111px;background:var(--tan)}

.brand-mark{left:86px;top:34px;width:70px;height:70px;background:var(--green);border:3px solid var(--gold)}
.brand-name{left:178px;top:36px;font-family:"Libre Baskerville",serif;font-size:17px;line-height:19px;color:var(--gold)}
.tagline{right:85px;top:30px;font-family:"Yanone Kaffeesatz",sans-serif;font-size:20px;color:var(--tan-text)}
.social-top{left:738px;top:72px;display:flex;gap:4px}
.social-top span{width:23px;height:23px;border-radius:50%;background:var(--tan-text);display:block}

.main-nav{left:76px;top:136px;width:777px;height:38px;border-radius:4px;
  background:linear-gradient(#1d5a35,var(--green-dark));display:flex;align-items:center;justify-content:space-around;padding:0 10px}
.main-nav a{font-family:"Ubuntu",sans-serif;font-size:14px;color:var(--white);text-decoration:none}

.hero-frame{left:75px;top:179px;width:776px;height:290px;background:var(--white);border-radius:5px;box-shadow:0 6px 8px rgba(0,0,0,.12)}
.hero{left:82px;top:184px;width:764px;height:281px;background:var(--green)}
.hero-title{left:121px;top:250px;font-family:"Ubuntu",sans-serif;font-style:italic;font-weight:500;font-size:20px;line-height:25px;color:var(--white)}
.hero-text{left:121px;top:312px;width:270px;font-family:"Ubuntu",sans-serif;font-style:italic;font-size:9.3px;line-height:12.7px;color:var(--white);letter-spacing:-.2px}
.btn-learn{left:120px;top:386px;width:92px;height:24px;border-radius:5px;background:var(--green-soft);color:var(--white);
  font-family:"Ubuntu",sans-serif;font-size:13px;line-height:24px;text-align:center}
.dot{top:431px;width:10px;height:10px;border-radius:50%;background:#f1dcc0}
.dot.off{background:var(--green-soft)}
.hero-photo{left:424px;top:197px;width:403px;height:246px;border:5px solid #5b8a6c;
  background:linear-gradient(160deg,#cfd6d3 0%,#6f8a5b 40%,#d9c55a 70%,#2f3a2f 100%)}
.play{left:608px;top:292px}

.card{background:var(--white);border-radius:6px;box-shadow:0 6px 8px rgba(0,0,0,.08)}
.featured-article{left:73px;top:483px;width:614px;height:200px}
.heading{font-family:"Yanone Kaffeesatz",sans-serif;font-weight:500;color:var(--heading)}
.fa-heading{left:95px;top:496px;font-size:23px}
.body-text{font-size:10.5px;line-height:17.8px;color:var(--ink);text-align:justify}
.fa-text{left:95px;top:531px;width:440px}
.btn-dark{background:var(--green);color:var(--white);border-radius:7px;text-align:center;font-size:10.5px}
.btn-view{left:94px;top:627px;width:72px;height:27px;line-height:27px}
.fa-photo{left:551px;top:518px;width:124px;height:140px;border:3px solid var(--white);box-shadow:0 0 4px rgba(0,0,0,.35);border-radius:4px;
  background:linear-gradient(170deg,#8a5a3a,#c9b8a0 50%,#e7e3dc)}

.side-heading{font-size:17px}
.nl-heading{left:699px;top:489px}
.nl-text{left:699px;top:518px;font-family:"Ubuntu",sans-serif;font-size:10.5px;color:#444}
.nl-input{left:693px;top:539px;width:155px;height:27px;border-radius:6px;background:var(--white);
  font-family:"Ubuntu",sans-serif;font-size:9.5px;line-height:27px;padding-left:11px;color:#333}
.btn-subscribe{left:697px;top:574px;width:68px;height:21px;line-height:21px;border-radius:5px;background:var(--green);color:var(--white);
  font-family:"Ubuntu",sans-serif;font-size:11px;text-align:center}
.btn-donate{left:699px;top:612px;width:148px;height:59px;border-radius:6px;background:linear-gradient(#a3223a,var(--maroon-dark));
  box-shadow:0 2px 4px rgba(0,0,0,.25);font-family:"Yanone Kaffeesatz",sans-serif;font-size:23px;line-height:59px;color:#f8ead5;text-align:center}

.current-needs{left:74px;top:695px;width:297px;height:249px}
.cn-heading{left:87px;top:706px;font-size:18px}
.cn-photo{left:87px;top:734px;width:78px;height:76px;border:3px solid var(--white);border-radius:4px;box-shadow:0 0 4px rgba(0,0,0,.35);
  background:linear-gradient(150deg,#e6e2da,#c8463c 60%,#b72e2a)}
.cn-text-a{left:172px;top:732px;width:185px}
.cn-text-b{left:91px;top:823px;width:266px}
.cn-meta{left:94px;top:908px;font-size:10.3px;color:#111}

.featured-event{left:384px;top:695px;width:297px;height:249px}
.fe-heading{left:400px;top:706px;font-size:18px}
.fe-logo{left:424px;top:730px;width:178px;height:90px;border-radius:8px;background:linear-gradient(#e9a25a,#3f7a3a 55%,#f2d14d)}
.fe-text{left:402px;top:832px;width:275px;font-style:italic;font-size:11.4px;line-height:19.5px;color:var(--red-text);font-family:"Ubuntu",sans-serif}
.btn-read{left:398px;top:904px;width:68px;height:21px;line-height:21px;font-family:"Ubuntu",sans-serif}

.contact-heading{left:700px;top:706px}
.contact-list{left:702px;top:731px;font-family:"Ubuntu",sans-serif;font-size:10.3px;line-height:14px;color:#333;list-style:none}
.contact-list li{display:flex;align-items:flex-start;gap:6px}
.contact-list li.gap{margin-top:2px}
.contact-list svg{flex:none;margin-top:2px}
.contact-list .blank{width:10px;flex:none}
.map{left:700px;top:830px;width:169px;height:93px;border:2px solid #d8d8d2;border-radius:4px;background:linear-gradient(135deg,#e4e8dc,#d9dccf 50%,#f0e7b8)}

.partners-label{left:118px;top:1012px;font-family:"Libre Baskerville",serif;font-size:18px;color:#555}
.badge{background:var(--badge);border-radius:4px;opacity:.85}

.footer-links{left:69px;top:1128px;display:flex;gap:9px;font-size:10px;color:var(--white)}
.footer-links a{color:var(--white);text-decoration:none}
.copyright{left:69px;top:1153px;font-size:10px;color:var(--white)}
.social-foot{left:703px;top:1113px;display:flex;gap:8px}
.social-foot span{width:33px;height:33px;border-radius:50%;background:var(--white);box-shadow:0 1px 3px rgba(0,0,0,.2);display:block}
</style>
</head>
<body>
<div class="abs top-band"></div>
<div class="abs footer-band"></div>

<header>
  <div class="abs brand-mark"></div>
  <div class="abs brand-name">Harvest<br>Hope<br>Outreach<br>House</div>
  <div class="abs tagline">Mercy at Work Since 1996</div>
  <div class="abs social-top" aria-label="Social links"><span></span><span></span><span></span><span></span></div>
  <nav class="abs main-nav">
    <a href="#">Home</a><a href="#">How to Help</a><a href="#">Programs</a><a href="#">News &amp; Events</a><a href="#">Our Partners</a><a href="#">About us</a><a href="#">Contact</a>
  </nav>
</header>

<section>
  <div class="abs hero-frame"></div>
  <div class="abs hero"></div>
  <h1 class="abs hero-title">Harvest Hope Outreach House<br>- Valley Grange Food Drive</h1>
  <p class="abs hero-text">Along the bank of the river, on this side and that, will grow all kinds of trees used for food; their leaves will not wither, and their fruit will not fail. They will bear fruit every month, because their water flows from the sanctuary. Their fruit will be for food, and their leaves for medicine. - Ezekiel 47:12</p>
  <div class="abs btn-learn">Learn more</div>
  <span class="abs dot" style="left:123px"></span>
  <span class="abs dot" style="left:137px"></span>
  <span class="abs dot off" style="left:152px"></span>
  <div class="abs hero-photo" role="img" aria-label="Photo of volunteers in yellow shirts presenting a donation cheque outside the food pantry"></div>
  <svg class="abs play" width="40" height="40" viewBox="0 0 40 40"><circle cx="20" cy="20" r="18" fill="rgba(255,255,255,.35)" stroke="#6f9a80" stroke-width="3"/><path d="M16 12 L28 20 L16 28Z" fill="#13472a"/></svg>
</section>

<section>
  <div class="abs card featured-article"></div>
  <h2 class="abs heading fa-heading">Featured Article</h2>
  <p class="abs body-text fa-text">Mauris non mi id tellus ultrices laoreet sit amet aliquet leo. Maecenas vehicula mi in urna egestas convallis. Mauris porta risus et nisi pharetra sagittis adipiscing urna laoreet. Proin sit amet lorem venenatis est rutrum consequat id eu urna. Nam nec mi nisl, vel laoreet leo. Vivamus vulputate adipiscing lorem tincidunt vehicula. Mauris quis ante odio. Nullam posuere venenatis magna quis facilisis. Ut leo elit, aliquam non suscipit.</p>
  <div class="abs btn-dark btn-view">View more</div>
  <div class="abs fa-photo" role="img" aria-label="Photo of chefs preparing trays of food"></div>
</section>

<aside>
  <h3 class="abs heading side-heading nl-heading">NEWSLETTER</h3>
  <p class="abs nl-text">Subscribe to our newsletter:</p>
  <div class="abs nl-input">Email Id</div>
  <div class="abs btn-subscribe">Subscribe</div>
  <div class="abs btn-donate">Donate Now</div>

  <h3 class="abs heading side-heading contact-heading">CONTACT ME</h3>
  <ul class="abs contact-list">
    <li><svg width="10" height="10" viewBox="0 0 10 10"><path d="M5 0 L10 5 H8.5 V10 H1.5 V5 H0Z" fill="#555"/></svg>42 Willowbank Rd</li>
    <li><span class="blank"></span>Ashford</li>
    <li><span class="blank"></span>Ohio 452110</li>
    <li class="gap"><svg width="10" height="10" viewBox="0 0 10 10"><path d="M2 0 L4 3 L3 4 Q4.5 6.5 6 7 L7 6 L10 8 L8.5 10 Q2 9 0 1.5Z" fill="#555"/></svg>+1 800 555 0142</li>
    <li><svg width="10" height="10" viewBox="0 0 10 10"><path d="M2 0 H6.5 L9 2.5 V10 H2Z" fill="#555"/></svg>+1 504 555 0187</li>
    <li><svg width="10" height="10" viewBox="0 0 10 10"><rect x="0" y="2" width="10" height="7" fill="#555"/><path d="M0 2 L5 6 L10 2" stroke="#fff" fill="none"/></svg>hello@hhohbriel.org</li>
  </ul>
  <div class="abs map" role="img" aria-label="Street map showing the center's location"></div>
</aside>

<section>
  <div class="abs card current-needs"></div>
  <h2 class="abs heading cn-heading">Current Needs</h2>
  <div class="abs cn-photo" role="img" aria-label="Photo of children with donated supplies"></div>
  <p class="abs body-text cn-text-a">Mauris porta risus et nisi pharetra sagittis adipiscing urna laoreet. Proin sit amet lorem venenatis est rutrum consequat id eu urna. Nam nec mi nisl, vel laoreet leo. lorem tincidunt vehicula.</p>
  <p class="abs body-text cn-text-b">Mauris porta risus et nisi pharetra sagittis adipiscing urna laoreet. Proin sit amet lorem venenatis est rutrum consequat id eu urna. Nam nec mi nisl, vel laoreet leo. lorem tincidunt vehicula.</p>
  <p class="abs cn-meta">http://www.hhohbriel.org &nbsp;- &nbsp;22-01-2013 &nbsp;- &nbsp;1 month ago</p>

  <div class="abs card featured-event"></div>
  <h2 class="abs heading fe-heading">Featured Event</h2>
  <div class="abs fe-logo" role="img" aria-label="Gather at the Hearth event emblem with harvest produce"></div>
  <p class="abs fe-text">THANK YOU TO MEADOW OAK AND EVERYONE WHO HELPED MAKE OUR FIRST FARM-TO-TABLE EVENT A SUCCESS!</p>
  <div class="abs btn-dark btn-read">Read more</div>
</section>

<section aria-label="Partners">
  <p class="abs partners-label">Partners</p>
  <div class="abs badge" style="left:214px;top:984px;width:45px;height:61px"></div>
  <div class="abs badge" style="left:291px;top:994px;width:77px;height:47px"></div>
  <div class="abs badge" style="left:402px;top:986px;width:131px;height:61px"></div>
  <div class="abs badge" style="left:563px;top:998px;width:83px;height:36px"></div>
  <div class="abs badge" style="left:665px;top:975px;width:141px;height:81px"></div>
</section>

<footer>
  <nav class="abs footer-links">
    <a href="#">Home</a><span>|</span><a href="#">How to Help</a><span>|</span><a href="#">Programs</a><span>|</span><a href="#">News &amp; Events</a><span>|</span><a href="#">Our Partners</a><span>|</span><a href="#">About us</a><span>|</span><a href="#">Contact</a>
  </nav>
  <p class="abs copyright">Copyright &nbsp;© &nbsp;2013 &nbsp;&nbsp;www.hhohbriel.org &nbsp;&nbsp;&nbsp;All rights reserved.</p>
  <div class="abs social-foot" aria-label="Social links"><span></span><span></span><span></span><span></span></div>
</footer>
</body>
</html>
```